Brintel Works - Fast, Efficient and Gas Mainteance for Domestic, Commercial and Industrial clients

We are in the process of purchasing a new business and would like to get a new logo and business card.
Business is a gas maintenance business that also does new gas installations.
Has been established since 1988.
Services include:
Install all types of gas appliances & equipment inc. hot water units
Maintain / repair / replace all types of gas appliances & equipment

Target Market(s)

Domestic, Commercial and Industrial clients

Industry/Entity Type

Business

Contact Information for Business Card

admin@brintelworks.com.au
07 3918 4726
Brintel Works PTY LTD

Logo Text

Gas Fitting & Plumbing Maintenance Specialists

Font styles to use
Sans Serif

Requirements
Must have
• Logo
• Business name, contact number, email address, web address
• Domestic | Commercial | Industrial Est Since 1988
Nice to have
• Possibly a black card with a flame logo to one side
Should not have
• Spelling errors

```html
<!DOCTYPE html>
<html lang="en">
<head>
<meta charset="utf-8">
<title>Brintel Works PTY LTD – Business Card</title>
<link rel="stylesheet" href="https://fonts.googleapis.com/css2?family=Poppins:wght@600;700&family=Open+Sans:wght@400;700&display=swap">
<style>
  :root {
    --stage: #ecebe8;
    --card-black: #000000;
    --flame-orange: #f37021;
    --flame-red: #ec2a24;
    --flame-yellow: #ffd21f;
    --name-amber: #f9a21b;
    --white: #ffffff;
  }
  * { box-sizing: border-box; margin: 0; padding: 0; }
  html, body { width: 1200px; height: 900px; overflow: hidden; }
  body {
    background: var(--stage);
    position: relative;
    font-family: "Open Sans", sans-serif;
  }
  .card {
    position: absolute;
    border-radius: 14px;
    overflow: hidden;
    box-shadow: 0 10px 26px rgba(0,0,0,0.22);
  }
  .card-back { left: 78px; top: 34px; width: 588px; height: 364px; background: var(--card-black); }
  .card-front {
    left: 389px; top: 506px; width: 566px; height: 350px;
    background: linear-gradient(180deg, var(--flame-orange) 0%, var(--flame-red) 100%);
  }
  .card-art { position: absolute; inset: 0; }
  .brand {
    position: absolute; left: 0; right: 0; text-align: center;
    font-family: "Poppins", sans-serif; font-weight: 700; line-height: 1;
  }
  .brand-name { font-size: 38px; letter-spacing: 0.2px; }
  .brand-suffix { font-size: 14px; letter-spacing: 3px; }
  .card-back .brand-name { top: 168px; color: var(--name-amber); }
  .card-back .brand-suffix { top: 212px; color: var(--name-amber); }
  .card-front .brand-name { top: 200px; color: var(--flame-yellow); }
  .card-front .brand-suffix { top: 245px; color: var(--flame-yellow); }

  .address {
    position: absolute; left: 32px; top: 277px;
    color: var(--white); font-size: 16px; line-height: 24px;
  }
  .contact-list {
    position: absolute; right: 36px; top: 266px;
    list-style: none; color: var(--white); font-size: 16px; line-height: 24.5px; text-align: right;
  }
  .contact-list li { display: flex; justify-content: flex-end; align-items: center; gap: 10px; }
  .contact-icon { width: 13px; height: 13px; flex: none; }
  .tagline {
    position: absolute; left: 0; right: 0; top: 290px; text-align: center;
    color: var(--white); font-weight: 700; font-size: 17.5px;
  }
</style>
</head>
<body>

<section class="card card-back" aria-label="Business card, contact side">
  <svg class="card-art" viewBox="0 0 588 364" width="588" height="364" aria-hidden="true">
    <defs>
      <linearGradient id="bandFlame" x1="0" y1="0" x2="0" y2="1">
        <stop offset="0" stop-color="#f37021"/>
        <stop offset="1" stop-color="#ec2a24"/>
      </linearGradient>
    </defs>
    <rect x="0" y="34" width="588" height="118" fill="url(#bandFlame)"/>
    <rect x="0" y="32" width="588" height="4" fill="#ffd21f"/>
    <rect x="0" y="150" width="588" height="4" fill="#ffd21f"/>
    <circle cx="294" cy="92" r="92" fill="#000000"/>
  </svg>
  <div class="brand brand-name">Brintel Works</div>
  <div class="brand brand-suffix">PTY LTD</div>

  <address class="address" style="font-style:normal">
    12345, Address Goes Here<br>
    Country Name, 123456
  </address>

  <ul class="contact-list">
    <li>07 3918 4726
      <svg class="contact-icon" viewBox="0 0 24 24" aria-hidden="true"><path fill="#f9a21b" d="M6.6 10.8a15.1 15.1 0 0 0 6.6 6.6l2.2-2.2c.3-.3.7-.4 1-.2 1.1.4 2.3.6 3.6.6.6 0 1 .4 1 1V20c0 .6-.4 1-1 1A17 17 0 0 1 3 4c0-.6.4-1 1-1h3.5c.6 0 1 .4 1 1 0 1.2.2 2.4.6 3.6.1.3 0 .7-.2 1z"/></svg>
    </li>
    <li>admin@brintelworks.com.au
      <svg class="contact-icon" viewBox="0 0 24 24" aria-hidden="true"><rect x="2" y="5" width="20" height="14" rx="1.5" fill="#f9a21b"/><path d="M2.5 6l9.5 7 9.5-7" fill="none" stroke="#000" stroke-width="1.6"/></svg>
    </li>
    <li>www.brintelworks.com.au
      <svg class="contact-icon" viewBox="0 0 24 24" aria-hidden="true"><g fill="none" stroke="#f9a21b" stroke-width="2.6" stroke-linecap="round"><path d="M10 14a4 4 0 0 0 5.7 0l3.5-3.5a4 4 0 0 0-5.7-5.7l-1.2 1.2"/><path d="M14 10a4 4 0 0 0-5.7 0l-3.5 3.5a4 4 0 0 0 5.7 5.7l1.2-1.2"/></g></svg>
    </li>
  </ul>
</section>

<section class="card card-front" aria-label="Business card, brand side">
  <svg class="card-art" viewBox="0 0 566 350" width="566" height="350" aria-hidden="true">
    <rect x="0" y="82" width="566" height="94" fill="#000000"/>
    <rect x="0" y="79" width="566" height="4" fill="#ffd21f"/>
    <rect x="0" y="175" width="566" height="4" fill="#ffd21f"/>
    <circle cx="283" cy="122" r="74" fill="#f15a22" stroke="#ffd21f" stroke-width="3"/>
  </svg>
  <div class="brand brand-name">Brintel Works</div>
  <div class="brand brand-suffix">PTY LTD</div>
  <p class="tagline">Domestic | Commercial | Industrial Est Since 1988</p>
</section>

</body>
</html>
```